Flyer Design for Private Car Service

Flyer should cater to Business Travelers and Executives who travel Business Class or First Class.
Flyer should include images attached.
Flyer should include the below text
Dallas to Austin
Quorvan Ride
• Travel Dallas to Austin in a new 2025 Norvak Tressel for $499 one-way
• Trip includes a Uniformed Chauffeur who has a Commercial Drivers License (CDL)
• You can Schedule Chauffeur Pickup at Your Home in Dallas
• Our Chauffeur will Drop You Off at Your Final Destination in Austin
• You can Schedule Chauffeur Return Pickup in Austin and Return Back to Dallas.
• We offer Faster Times on Door-to-Door Travel than Bluequill Airways
• We offer Comparable Prices on Door-to-Door Travel Times than Bluequill Airways
• All of our trips are insured with $500k of commercial auto insurance
• Our Passengers can Talk on Cell Phone & Conduct Kavlo calls Throughout Travel
• Our Passengers have Maximum Privacy, Comfort and First-Class Amenities.
• Our Passengers Avoid Marrow Pike Airfield and QHN Airport hassles & delays
• Member Tellbrook Chamber of Commerce, Pindle Chamber of Commerce.
• Book your trip today at www.quorvanride.example
Target Market(s)
Business Travelers
Look and feel

```html
<!DOCTYPE html>
<html lang="en">
<head>
<meta charset="utf-8">
<title>Dallas to Austin Quorvan Ride Flyer</title>
<link href="https://fonts.googleapis.com/css2?family=Orbitron:wght@700;900&family=Poppins:wght@400;500;700;800&display=swap" rel="stylesheet">
<style>
  :root {
    --ink: #1d1d1f;
    --red: #e3262b;
    --paper: #f4f4f4;
    --white: #ffffff;
    --stage: #959595;
  }
  * { margin: 0; padding: 0; box-sizing: border-box; }
  html, body {
    width: 1040px; height: 1200px; overflow: hidden;
    background: var(--stage);
    font-family: "Poppins", sans-serif;
    color: var(--ink);
  }
  .flyer {
    position: absolute; left: 70px; top: 18px;
    width: 900px; height: 1164px;
    overflow: hidden;
    background: var(--paper);
  }
  .flyer-bg { position: absolute; inset: 0; width: 900px; height: 1164px; }
  .headline {
    position: absolute; left: 0; right: 0; top: 34px;
    text-align: center; color: var(--white);
    font-family: "Orbitron", sans-serif;
  }
  .headline-route {
    display: block; font-size: 22px; font-weight: 700; letter-spacing: 2px; line-height: 28px;
  }
  .headline-main {
    display: block; font-size: 44px; font-weight: 900; letter-spacing: 2px; line-height: 52px; margin-top: 4px;
  }
  .brand {
    position: absolute; left: 0; right: 0; top: 176px; text-align: center;
  }
  .brand-mark {
    width: 46px; height: 46px; border-radius: 50%;
    background: var(--red); margin: 0 auto 14px;
  }
  .brand-name {
    font-size: 38px; font-weight: 500; letter-spacing: 3px; color: var(--ink); line-height: 44px;
  }
  .features { position: absolute; top: 334px; left: 0; width: 900px; }
  .feature { position: absolute; display: flex; align-items: center; height: 86px; }
  .feature-icon { width: 74px; height: 74px; flex: none; }
  .feature-text {
    margin-left: 14px; width: 296px;
    font-size: 16.8px; font-weight: 500; line-height: 20.8px; color: var(--ink);
  }
  .feature-text em { font-style: normal; color: var(--red); }
  .col-left { left: 57px; width: 384px; }
  .col-right { left: 491px; width: 384px; }
  .photo-strip { position: absolute; top: 872px; left: 58px; width: 804px; height: 131px; }
  .photo {
    position: absolute; top: 0; height: 131px; width: 262px;
    border-radius: 4px; border: 1px solid #c9c9c9;
  }
  .photo-1 { left: 0; background: linear-gradient(135deg, #6b6e73, #1c1c1f 60%, #3e3f43); }
  .photo-2 { left: 271px; background: linear-gradient(180deg, #cfc9c2 0%, #bdb6ad 55%, #e2e1df 100%); }
  .photo-3 { left: 542px; background: linear-gradient(135deg, #8a98a8, #2a2b2e 45%, #1a1a1b); }
  .cta-pill {
    position: absolute; left: 247px; top: 1045px; width: 406px; height: 44px;
    background: var(--red); border-radius: 0 0 16px 16px;
    color: var(--white); font-weight: 800; font-size: 22px; letter-spacing: 1.5px;
    display: flex; align-items: center; justify-content: center;
  }
  .cta-url {
    position: absolute; left: 0; right: 0; top: 1098px;
    display: flex; align-items: center; justify-content: center; gap: 10px;
    color: var(--white); font-weight: 800; font-size: 34px; letter-spacing: 0.5px;
  }
  .cta-url svg { width: 32px; height: 32px; }
</style>
</head>
<body>
<div class="flyer">
  <svg class="flyer-bg" viewBox="0 0 900 1164" aria-hidden="true">
    <defs>
      <linearGradient id="headerShade" x1="0" y1="0" x2="1" y2="1">
        <stop offset="0" stop-color="#1a1a1b"/>
        <stop offset="0.5" stop-color="#3b3b3e"/>
        <stop offset="1" stop-color="#0e0e0f"/>
      </linearGradient>
      <linearGradient id="redBand" x1="0" y1="0" x2="1" y2="0">
        <stop offset="0" stop-color="#e3262b"/>
        <stop offset="0.5" stop-color="#f28d8d"/>
        <stop offset="1" stop-color="#e3262b"/>
      </linearGradient>
      <linearGradient id="paperShade" x1="0" y1="0" x2="1" y2="0">
        <stop offset="0" stop-color="#efefef"/>
        <stop offset="0.5" stop-color="#fbfbfb"/>
        <stop offset="1" stop-color="#efefef"/>
      </linearGradient>
    </defs>
    <rect width="900" height="1164" fill="url(#headerShade)"/>
    <path d="M0,262 C150,190 330,132 450,130 C570,132 750,188 900,262 L900,1164 L0,1164 Z" fill="#ffffff"/>
    <path d="M0,282 C150,210 330,142 450,140 C570,142 750,208 900,282" fill="none" stroke="url(#redBand)" stroke-width="12"/>
    <path d="M0,300 C150,228 330,152 450,152 C570,152 750,226 900,300 L900,1164 L0,1164 Z" fill="url(#paperShade)"/>
    <path d="M0,1062 Q450,1018 900,1062 L900,1164 L0,1164 Z" fill="#ffffff"/>
    <path d="M0,1060 Q450,1016 900,1060" fill="none" stroke="#e3262b" stroke-width="7"/>
    <path d="M0,1068 Q450,1030 900,1068 L900,1164 L0,1164 Z" fill="url(#headerShade)"/>
    <line x1="450" y1="330" x2="450" y2="850" stroke="#e2e2e2" stroke-width="1.5"/>
  </svg>

  <header class="headline">
    <span class="headline-route">DALLAS TO AUSTIN</span>
    <span class="headline-main">QUORVAN RIDE</span>
  </header>

  <div class="brand">
    <div class="brand-mark"></div>
    <div class="brand-name">QUORVAN RIDE</div>
  </div>

  <section class="features">
    <div class="feature col-left" style="top:0">
      <svg class="feature-icon" viewBox="0 0 74 74"><circle cx="37" cy="37" r="35.5" fill="#fff" stroke="#222" stroke-width="2"/><circle cx="37" cy="37" r="31" fill="#e3262b"/><g fill="none" stroke="#fff" stroke-width="2" stroke-linejoin="round"><path d="M37 20c-6 0-11 5-11 11 0 8 11 20 11 20s11-12 11-20c0-6-5-11-11-11z"/><circle cx="37" cy="31" r="4"/><path d="M22 54h30"/></g></svg>
      <p class="feature-text">Travel Dallas to Austin in a new 2025 Norvak Tressel for <em>$499</em> one-way</p>
    </div>
    <div class="feature col-left" style="top:86px">
      <svg class="feature-icon" viewBox="0 0 74 74"><circle cx="37" cy="37" r="35.5" fill="#fff" stroke="#222" stroke-width="2"/><circle cx="37" cy="37" r="31" fill="#e3262b"/><g fill="none" stroke="#fff" stroke-width="2" stroke-linejoin="round"><path d="M22 46v-6l4-8h22l4 8v6z"/><circle cx="28" cy="46" r="3"/><circle cx="46" cy="46" r="3"/><rect x="36" y="20" width="16" height="10" rx="2"/><path d="M39 24h10"/></g></svg>
      <p class="feature-text">Trip includes a Uniformed Chauffeur who has a Commercial Drivers License (CDL)</p>
    </div>
    <div class="feature col-left" style="top:172px">
      <svg class="feature-icon" viewBox="0 0 74 74"><circle cx="37" cy="37" r="35.5" fill="#fff" stroke="#222" stroke-width="2"/><circle cx="37" cy="37" r="31" fill="#e3262b"/><g fill="none" stroke="#fff" stroke-width="2"><rect x="20" y="22" width="28" height="26" rx="2"/><path d="M20 29h28M26 19v6M42 19v6"/><circle cx="47" cy="47" r="8" fill="#e3262b"/><path d="M47 43v4l3 2"/></g></svg>
      <p class="feature-text">You can Schedule Chauffeur Pickup at Your Home in Dallas</p>
    </div>
    <div class="feature col-left" style="top:258px">
      <svg class="feature-icon" viewBox="0 0 74 74"><circle cx="37" cy="37" r="35.5" fill="#fff" stroke="#222" stroke-width="2"/><circle cx="37" cy="37" r="31" fill="#e3262b"/><g fill="none" stroke="#fff" stroke-width="2"><circle cx="39" cy="41" r="13"/><path d="M26 41h26M39 28c-5 5-5 21 0 26M39 28c5 5 5 21 0 26"/><path d="M28 16c-4 0-7 3-7 7 0 5 7 12 7 12s7-7 7-12c0-4-3-7-7-7z" fill="#e3262b"/><circle cx="28" cy="23" r="2.5"/></g></svg>
      <p class="feature-text">Our Chauffeur will Drop You Off at Your Final Destination in Austin</p>
    </div>
    <div class="feature col-left" style="top:344px">
      <svg class="feature-icon" viewBox="0 0 74 74"><circle cx="37" cy="37" r="35.5" fill="#fff" stroke="#222" stroke-width="2"/><circle cx="37" cy="37" r="31" fill="#e3262b"/><g fill="none" stroke="#fff" stroke-width="2" stroke-linecap="round" stroke-linejoin="round"><path d="M22 30h26l-5-5M52 44H26l5 5"/></g></svg>
      <p class="feature-text">You can Schedule Chauffeur Return Pickup in Austin and Return Back to Dallas.</p>
    </div>
    <div class="feature col-left" style="top:430px">
      <svg class="feature-icon" viewBox="0 0 74 74"><circle cx="37" cy="37" r="35.5" fill="#fff" stroke="#222" stroke-width="2"/><circle cx="37" cy="37" r="31" fill="#e3262b"/><g fill="none" stroke="#fff" stroke-width="2" stroke-linecap="round"><circle cx="40" cy="40" r="13"/><path d="M40 33v7l5 3M37 22h6M40 22v5M18 36h8M16 42h8M20 48h6"/></g></svg>
      <p class="feature-text">We offer Faster Times on Door-to-Door Travel than Bluequill Airways</p>
    </div>

    <div class="feature col-right" style="top:0">
      <svg class="feature-icon" viewBox="0 0 74 74"><circle cx="37" cy="37" r="35.5" fill="#fff" stroke="#222" stroke-width="2"/><circle cx="37" cy="37" r="31" fill="#e3262b"/><g fill="none" stroke="#fff" stroke-width="2" stroke-linecap="round"><circle cx="42" cy="30" r="11"/><path d="M45 25h-4a2.5 2.5 0 0 0 0 5h2a2.5 2.5 0 0 1 0 5h-4M42 22v3M42 35v3"/><path d="M20 40h6v14h-6zM26 42l6-4h8v4h-6"/></g></svg>
      <p class="feature-text">We offer Comparable Prices on Door-to-Door Travel Times than Bluequill Airways</p>
    </div>
    <div class="feature col-right" style="top:86px">
      <svg class="feature-icon" viewBox="0 0 74 74"><circle cx="37" cy="37" r="35.5" fill="#fff" stroke="#222" stroke-width="2"/><circle cx="37" cy="37" r="31" fill="#e3262b"/><g fill="none" stroke="#fff" stroke-width="2" stroke-linejoin="round"><rect x="22" y="18" width="24" height="34" rx="2"/><path d="M27 26h14M27 32h14M27 38h8"/><path d="M40 24l4 4 7-8" stroke-linecap="round"/><path d="M36 52v-4l3-5h12l3 5v4z" fill="#e3262b"/></g></svg>
      <p class="feature-text">All of our trips are insured with <em>$500k</em> of commercial auto insurance</p>
    </div>
    <div class="feature col-right" style="top:172px">
      <svg class="feature-icon" viewBox="0 0 74 74"><circle cx="37" cy="37" r="35.5" fill="#fff" stroke="#222" stroke-width="2"/><circle cx="37" cy="37" r="31" fill="#e3262b"/><g fill="none" stroke="#fff" stroke-width="2"><circle cx="28" cy="28" r="7"/><circle cx="46" cy="28" r="7"/><circle cx="28" cy="46" r="7"/><circle cx="46" cy="46" r="7"/><path d="M43 44c1 3 3 5 6 5"/><path d="M24 26l4 3 4-3"/></g></svg>
      <p class="feature-text">Our Passengers can Talk on Cell Phone &amp; Conduct Kavlo calls Throughout Travel</p>
    </div>
    <div class="feature col-right" style="top:258px">
      <svg class="feature-icon" viewBox="0 0 74 74"><circle cx="37" cy="37" r="35.5" fill="#fff" stroke="#222" stroke-width="2"/><circle cx="37" cy="37" r="31" fill="#e3262b"/><g fill="none" stroke="#fff" stroke-width="2" stroke-linejoin="round"><path d="M37 17l15 6v12c0 10-7 17-15 21-8-4-15-11-15-21V23z"/><circle cx="37" cy="32" r="4"/><path d="M30 44c1-4 4-6 7-6s6 2 7 6"/></g></svg>
      <p class="feature-text">Our Passengers have Maximum Privacy, Comfort and First-Class Amenities.</p>
    </div>
    <div class="feature col-right" style="top:344px">
      <svg class="feature-icon" viewBox="0 0 74 74"><circle cx="37" cy="37" r="35.5" fill="#fff" stroke="#222" stroke-width="2"/><circle cx="37" cy="37" r="31" fill="#e3262b"/><g fill="none" stroke="#fff" stroke-width="2" stroke-linejoin="round"><path d="M18 38l34-12c3-1 5 2 2 4L22 44l-4-2z"/><path d="M30 34l-6-8h4l10 5M36 40l2 8h-4l-6-6"/><circle cx="48" cy="47" r="7" fill="#e3262b"/><path d="M48 44v3l2 2"/></g></svg>
      <p class="feature-text">Our Passengers Avoid Marrow Pike Airfield and QHN Airport hassles &amp; delays</p>
    </div>
    <div class="feature col-right" style="top:430px">
      <svg class="feature-icon" viewBox="0 0 74 74"><circle cx="37" cy="37" r="35.5" fill="#fff" stroke="#222" stroke-width="2"/><circle cx="37" cy="37" r="31" fill="#e3262b"/><g fill="none" stroke="#fff" stroke-width="2"><circle cx="37" cy="26" r="6"/><circle cx="25" cy="34" r="4"/><circle cx="49" cy="34" r="4"/><path d="M28 52v-8c0-4 4-7 9-7s9 3 9 7v8M18 52v-6c0-3 3-5 7-5M56 52v-6c0-3-3-5-7-5"/></g></svg>
      <p class="feature-text">Member Tellbrook Chamber of Commerce, Pindle Chamber of Commerce.</p>
    </div>
  </section>

  <div class="photo-strip">
    <div class="photo photo-1" role="img" aria-label="Uniformed chauffeur opening the rear door of a black SUV for a business traveler"></div>
    <div class="photo photo-2" role="img" aria-label="Fleet of SUVs parked in a row with chauffeurs standing beside them"></div>
    <div class="photo photo-3" role="img" aria-label="Group of uniformed chauffeurs in black caps and coats"></div>
  </div>

  <div class="cta-pill">BOOK YOUR TRIP TODAY AT</div>
  <div class="cta-url">
    <svg viewBox="0 0 32 32" aria-hidden="true"><g fill="none" stroke="#fff" stroke-width="1.8"><circle cx="16" cy="16" r="13"/><path d="M3 16h26M16 3c-5 5-5 21 0 26M16 3c5 5 5 21 0 26M5 9h22M5 23h22"/></g></svg>
    <span>WWW.QUORVANRIDE.EXAMPLE</span>
  </div>
</div>
</body>
</html>
```